Velvette by Marisa Dunn business cards

I am after a business card that will fit the name of my business - velvette.
I want something classy and sexy and nothing tacky.
Ideas that I like are Zebra print backgrounds glitter back grounds
Two ideas I had were
1. Zebra print in black and white, the name Velvette by Marisa Dunn and a shilouette of a woman laying on top of the name. Or instead of zebra a glitter background.
2. Idea very similar except for instead of a woman a pair of lips maybe a hot pink glitter or a gold glitter depending on background with the business name between the lips.
Or you can do something completely different.

```html
<!DOCTYPE html>
<html lang="en">
<head>
<meta charset="utf-8">
<title>Velvette by Marisa Dunn – Business Card</title>
<link rel="stylesheet" href="https://fonts.googleapis.com/css2?family=Mulish:wght@300;400;800&display=swap">
<style>
  :root {
    --card-edge: #2f2b29;
    --card-mid: #4a4745;
    --card-glow: #62605e;
    --print-light: rgba(200, 198, 196, 0.42);
    --print-soft: rgba(200, 198, 196, 0.16);
    --text-name: #ffffff;
    --text-body: #dcdad8;
    --icon-line: #8c8a88;
  }
  html, body {
    margin: 0;
    padding: 0;
    width: 1200px;
    height: 685px;
    overflow: hidden;
    background: #ffffff;
  }
  .card {
    position: relative;
    width: 1200px;
    height: 685px;
    overflow: hidden;
    background: radial-gradient(ellipse 62% 78% at 52% 48%, var(--card-glow) 0%, var(--card-mid) 55%, var(--card-edge) 100%);
    font-family: "Mulish", "Century Gothic", sans-serif;
    color: var(--text-body);
  }
  .card__print {
    position: absolute;
    left: 300px;
    top: 20px;
    width: 600px;
    height: 665px;
    background:
      linear-gradient(120deg, rgba(200,198,196,0) 20%, var(--print-soft) 45%, var(--print-light) 55%, var(--print-soft) 65%, rgba(200,198,196,0) 85%),
      radial-gradient(ellipse 50% 50% at 50% 50%, var(--print-soft) 0%, rgba(200,198,196,0) 100%);
    -webkit-mask-image: radial-gradient(ellipse 50% 50% at 50% 50%, #000 40%, transparent 100%);
    mask-image: radial-gradient(ellipse 50% 50% at 50% 50%, #000 40%, transparent 100%);
  }
  .line {
    position: absolute;
    left: 0;
    width: 1200px;
    text-align: center;
    line-height: 1;
    white-space: nowrap;
  }
  .owner-name {
    top: 40px;
    font-size: 63px;
    font-weight: 800;
    color: var(--text-name);
    letter-spacing: 1.5px;
  }
  .owner-title {
    top: 100px;
    font-size: 53px;
    font-weight: 300;
    letter-spacing: 0.5px;
  }
  .contact {
    font-size: 45px;
    font-weight: 300;
    letter-spacing: 0.8px;
  }
  .contact--street { top: 230px; }
  .contact--city { top: 292px; }
  .contact--phone { top: 399px; }
  .contact--mobile { top: 492px; }
  .contact--email { top: 585px; }
  .icon {
    position: absolute;
    fill: none;
    stroke: var(--icon-line);
    stroke-width: 2;
    stroke-linejoin: round;
    stroke-linecap: round;
  }
  .icon--home { left: 127px; top: 213px; width: 68px; height: 68px; }
  .icon--phone { left: 129px; top: 398px; width: 62px; height: 48px; }
  .icon--mobile { left: 140px; top: 476px; width: 42px; height: 70px; }
  .icon--mail { left: 133px; top: 594px; width: 56px; height: 36px; }
</style>
</head>
<body>
  <main class="card">
    <div class="card__print" role="img" aria-label="Soft white zebra-print texture sweeping across the card centre"></div>

    <div class="line owner-name">Marisa Dunn</div>
    <div class="line owner-title">Proprietor</div>

    <svg class="icon icon--home" viewBox="0 0 68 68" aria-hidden="true">
      <path d="M4 34 L34 6 L64 34"/>
      <path d="M12 27 V64 H56 V27"/>
      <rect x="17" y="38" width="10" height="9"/>
      <rect x="41" y="38" width="10" height="9"/>
      <path d="M28 64 V44 H40 V64"/>
    </svg>
    <div class="line contact contact--street">18, Larkspur Ave</div>
    <div class="line contact contact--city">Westmere, CA 90412</div>

    <svg class="icon icon--phone" viewBox="0 0 62 48" aria-hidden="true">
      <path d="M3 16 C3 6 59 6 59 16 V20 H45 V14 H17 V20 H3 Z"/>
      <path d="M17 20 L9 44 H53 L45 20"/>
      <circle cx="31" cy="32" r="7"/>
    </svg>
    <div class="line contact contact--phone">555204718</div>

    <svg class="icon icon--mobile" viewBox="0 0 42 70" aria-hidden="true">
      <rect x="3" y="2" width="36" height="66" rx="5"/>
      <rect x="8" y="10" width="26" height="44"/>
      <circle cx="21" cy="61" r="3"/>
      <path d="M17 6 H25"/>
    </svg>
    <div class="line contact contact--mobile">555387926</div>

    <svg class="icon icon--mail" viewBox="0 0 56 36" aria-hidden="true">
      <rect x="2" y="2" width="52" height="32"/>
      <path d="M2 2 L28 22 L54 2"/>
      <path d="M2 34 L22 17"/>
      <path d="M54 34 L34 17"/>
    </svg>
    <div class="line contact contact--email">velvettebymd@velvettebymd.com</div>
  </main>
</body>
</html>
```